Podiatry clinic requires a modern revamp and editing of existing website.

I would like a fresh new look and updated information for my current business website. An easy to navigate site with prominent address and phone number for call to action. We are a podiatry clinic that focuses on general and sports podiatry.
I would like 4 pages; including Home page, About Us, Services & Contact.
www.brambleridgepodiatry.net

Target Market(s)

Active working professionals.

Industry/Entity Type

Medical

Coding

Coded - Design and coding required

Number of Pages Required

4 page

Font styles to use
Sans Serif

Colors
6b449b

Requirements
Must have
• A modern look with logo and active images; clean and uncluttered. Visible phone number and address for call to action.
• 4 pages - Home, About Us, Services, Contact.
• Home page - update address & service logos.
• About Us - update of personal information.
• Services - Revamp of existing page.
• Contact page to include Google map, email & phone number.
Nice to have
• Ability to add content easily; eg. a blog or adding video onto Home page.
• Link to Facebook page.

```html
<!DOCTYPE html>
<html lang="en">
<head>
<meta charset="utf-8">
<title>Bramble Ridge Podiatry</title>
<link href="https://fonts.googleapis.com/css2?family=Arimo:wght@400;700&display=swap" rel="stylesheet">
<style>
:root{
  --purple:#6b449b;
  --purple-form:#7f5aa8;
  --navy:#141a45;
  --ink:#222;
  --grey:#555;
  --light:#f4f4f6;
  --badge:#8d8d93;
  --white:#fff;
  --blue:#2a93d5;
}
*{box-sizing:border-box;margin:0;padding:0}
html,body{width:674px;height:1200px;overflow:hidden}
body{font-family:'Arimo',Arial,sans-serif;color:var(--ink);background:var(--white);position:relative}
.hero{position:absolute;left:0;top:0;width:674px;height:379px;
  background:
   radial-gradient(ellipse 260px 170px at 90px 90px,rgba(255,236,170,.75),rgba(255,236,170,0) 70%),
   linear-gradient(180deg,#717c88 0%,#9a9a8a 18%,#cdb679 38%,#b39450 55%,#7d6632 72%,#4a4225 88%,#37321d 100%)}
.brand{display:flex;align-items:center;gap:6px;font-weight:700;color:var(--white);font-size:15px;letter-spacing:.5px}
.brand-mark{width:16px;height:16px;border-radius:50%;background:var(--blue)}
.hero .brand{position:absolute;left:0;right:0;top:22px;justify-content:center}
.nav{position:absolute;top:50px;left:0;right:0;display:flex;justify-content:center;align-items:center;gap:22px;font-size:7px;font-weight:700;color:var(--white)}
.nav .cta{background:var(--purple);padding:7px 6px;border-radius:4px}
.hero-title{position:absolute;top:155px;width:100%;text-align:center;color:var(--white);font-size:38px;font-weight:700}
.hero-sub{position:absolute;top:211px;width:100%;text-align:center;color:var(--white);font-size:8px;font-weight:700;letter-spacing:2.2px}
.arrow{position:absolute;top:178px;width:22px;height:22px;background:rgba(40,40,40,.7);display:flex;align-items:center;justify-content:center}
.arrow.prev{left:10px}.arrow.next{right:10px}
.features{position:absolute;left:29px;top:311px;width:616px;height:140px;background:rgba(120,84,170,.93);display:flex;padding:30px 10px 0}
.feature{flex:1;text-align:center;color:var(--white);padding:0 8px}
.feature h3{font-size:12.5px;font-weight:700;margin-bottom:10px}
.feature p{font-size:7px;line-height:11px}
.intro{position:absolute;top:487px;left:30px;right:30px;text-align:center}
.intro h2{color:var(--navy);font-size:19px;font-weight:700;margin-bottom:20px}
.intro p{font-size:7.3px;line-height:13.5px;color:var(--grey)}
.intro strong{color:var(--ink)}
.appointment{position:absolute;top:605px;left:0;width:674px;height:228px;display:flex}
.appt-form{width:337px;height:228px;background:linear-gradient(100deg,#93709f 0%,#8a67aa 55%,#7551a8 100%);padding:30px 41px 0 34px;color:var(--white)}
.appt-form h2{font-size:19px;font-weight:700;text-align:center;margin-left:30px;margin-bottom:7px}
.row{display:flex;gap:16px;margin-bottom:8px}
.field{flex:1;height:18px;border:1px solid rgba(255,255,255,.8);font-size:7px;padding:4px 6px}
.field.msg{height:60px}
.submit{margin:9px 0 0 auto;width:70px;height:20px;background:var(--purple);font-size:7.5px;font-weight:700;display:flex;align-items:center;justify-content:center}
.appt-photo{width:337px;height:228px;
  background:
   radial-gradient(circle 70px at 245px 75px,#5a5e66 0%,#8a8d94 45%,rgba(138,141,148,0) 100%),
   radial-gradient(ellipse 90px 60px at 245px 200px,rgba(214,110,60,.55),rgba(214,110,60,0) 80%),
   linear-gradient(135deg,#ececef 0%,#d9dade 45%,#b7b9be 75%,#8f9299 100%)}
.partners{position:absolute;top:833px;left:0;width:674px;height:99px;background:var(--light);display:flex;align-items:center;justify-content:space-around;padding:0 30px}
.badge{display:flex;align-items:center;gap:5px}
.badge .dot{width:22px;height:22px;border-radius:50%;background:var(--badge)}
.badge .bar{height:20px;background:var(--badge);border-radius:2px}
.footer{position:absolute;top:932px;left:0;width:674px;height:223px;background:var(--purple);color:var(--white);display:flex;padding:42px 37px 0;gap:22px}
.col{width:132px;font-size:7px;line-height:11px}
.col h4{font-size:8.5px;font-weight:700;margin-bottom:7px}
.col h4::after{content:"";display:block;width:26px;height:1px;background:var(--white);margin-top:7px}
.social{display:flex;gap:5px;margin-top:10px}
.social span{width:18px;height:18px;background:rgba(255,255,255,.3)}
.contact-line{display:flex;gap:6px;align-items:flex-start;margin-top:6px}
.sched li{list-style:none;margin-bottom:8px}
.tag-row{display:flex;gap:3px;margin-bottom:3px}
.tag-row span{border:1px solid rgba(255,255,255,.6);padding:3px 7px;font-size:7px;line-height:10px}
.accept{font-weight:700;font-size:8.5px;margin:12px 0 7px}
.cards{display:flex;gap:6px}
.cards span{width:21px;height:13px;background:var(--white);border-radius:2px}
.bottom{position:absolute;top:1155px;left:0;width:674px;height:45px;text-align:center}
.bottom .brand{justify-content:center;color:var(--purple);margin-top:7px;font-size:13px}
.copy{font-size:6.5px;font-weight:700;color:var(--grey);margin-top:5px}
.copy b{color:var(--purple)}
</style>
</head>
<body>
<header class="hero" role="img" aria-label="Runner on a grassy hillside at sunrise">
  <div class="brand"><span class="brand-mark"></span>BRAMBLE RIDGE PODIATRY</div>
  <nav class="nav"><span>HOME</span><span>ABOUT US</span><span>SERVICES</span><span>BLOG</span><span class="cta">MAKE AN APPOINTMENT</span></nav>
  <h1 class="hero-title">Amazing Treatment</h1>
  <p class="hero-sub">Ridge is a corporate medical Health Center. You can Serve you 24/7</p>
  <span class="arrow prev"><svg width="8" height="8" viewBox="0 0 8 8"><path d="M5 1L2 4l3 3" stroke="#fff" fill="none" stroke-width="1.2"/></svg></span>
  <span class="arrow next"><svg width="8" height="8" viewBox="0 0 8 8"><path d="M3 1l3 3-3 3" stroke="#fff" fill="none" stroke-width="1.2"/></svg></span>
</header>
<section class="features">
  <div class="feature"><h3>Podiatry Treatments</h3><p>Podiatrits are trained to diagnose and trate all medical conditions that affect the feet and lower limb. At Bramble Ridge Podiatry we provide teatment for general &amp; Sports Podiatry conditions and veriuous specialsed treatments</p></div>
  <div class="feature"><h3>Podiatry Products Footwear</h3><p>At Bramble Ridge Podiatry we stock and recomment veriuus products and footwear that aid in maintaining optimal foot health</p></div>
  <div class="feature"><h3>Health Wellness Products</h3><p>At Bramble Ridge Podiatry, we believe that maintaining a healthy &amp; active lifestyle is the best way to prevent or manage debiliting foot conditions. We like to promote a healthy diet &amp; nutrition proper hydration and skin care</p></div>
</section>
<section class="intro">
  <h2>BRAMBLE RIDGE PODIATRY</h2>
  <p><strong>Bramble Ridge Podiatry</strong> is a Podiatry clinic in the heart of Ashvale city centre. We are located between Larkfield &amp; Orchard Streets in the Larkfield Commerce Centre. Our podiatrists are fully qualified health professionals who are able to diagnose, treat, manage or help to prevent all medical conditions that affect the feet and lower limb. We provide General Podiatry Treatment and some Specialised Services in relation to various foot conditions, including Sports Injuries, Orthotic Therapy and Nail Surgery.</p>
</section>
<section class="appointment">
  <form class="appt-form">
    <h2>MAKE AN APPOINTMENT</h2>
    <div class="row"><div class="field">First Name*</div><div class="field">Your Mail*</div></div>
    <div class="row"><div class="field">Appointment Date*</div><div class="field">Your Telephone*</div></div>
    <div class="field msg">Your Message</div>
    <div class="submit">SUBMIT NOW</div>
  </form>
  <div class="appt-photo" role="img" aria-label="Stethoscope and pens in a white coat pocket"></div>
</section>
<section class="partners">
  <div class="badge"><span class="dot"></span><span class="bar" style="width:100px"></span></div>
  <div class="badge"><span class="dot"></span><span class="bar" style="width:78px"></span></div>
  <div class="badge"><span class="bar" style="width:140px;height:26px"></span></div>
  <div class="badge"><span class="dot" style="width:16px;height:16px"></span><span class="bar" style="width:104px;height:32px"></span></div>
</section>
<footer class="footer">
  <div class="col"><h4>ABOUT US</h4><p>Lorem ipsum dolor sit amet, consectetur adipisicing elit. Beatae ducimus in enim quae commodi, rerum. Dolorum iusto id asperiores quis expedita harum assumenda, nesciunt sequi esse perspiciatis quisquam nobis, aliquam.</p>
    <div class="social"><span></span><span></span><span></span><span></span><span></span></div></div>
  <div class="col"><h4>GET IN TOUCH</h4><p>Bramble Ridge is one of the great Healthcase and Service Center</p>
    <div class="contact-line"><svg width="7" height="9" viewBox="0 0 7 9"><path d="M3.5 0A3.2 3.2 0 0 0 .3 3.2C.3 5.6 3.5 9 3.5 9S6.7 5.6 6.7 3.2A3.2 3.2 0 0 0 3.5 0zm0 4.5a1.3 1.3 0 1 1 0-2.6 1.3 1.3 0 0 1 0 2.6z" fill="#fff"/></svg><span>Level 4 / 27 Larkfield Lane<br>Ashvale 4021</span></div>
    <div class="contact-line"><svg width="8" height="8" viewBox="0 0 8 8"><path d="M1.6.2l1.3 1.7-.7 1.2a5 5 0 0 0 2.7 2.7l1.2-.7L7.8 6.4 6.9 7.8C3.4 7.8.2 4.6.2 1.1z" fill="#fff"/></svg><span>1300 555 019</span></div>
    <div class="contact-line"><svg width="9" height="7" viewBox="0 0 9 7"><rect x=".5" y=".5" width="8" height="6" fill="none" stroke="#fff"/><path d="M.5.5l4 3.2 4-3.2" fill="none" stroke="#fff"/></svg><span>info@brambleridgepodiatry.net</span></div></div>
  <div class="col"><h4>OUR SCHEDULE</h4><ul class="sched"><li>Sunday 9:00 am - 18:00 pm</li><li>Sunday 9:00 am - 18:00 pm</li><li>Sunday 9:00 am - 18:00 pm</li><li>Sunday 9:00 am - 18:00 pm</li><li>Sunday 9:00 am - 18:00 pm</li></ul></div>
  <div class="col"><h4>POPULAR TAGS</h4>
    <div class="tag-row"><span>Orthotics</span><span>Sports</span></div>
    <div class="tag-row"><span>Footwear</span><span>Nails</span></div>
    <div class="tag-row"><span>Heels</span><span>Kids</span><span>Gait</span></div>
    <p class="accept">We Accept</p><div class="cards"><span></span><span></span><span></span><span></span><span></span></div></div>
</footer>
<div class="bottom">
  <div class="brand"><span class="brand-mark"></span>BRAMBLE RIDGE PODIATRY</div>
  <p class="copy">©2016 <b>Bramble Ridge Podiatry.</b> All Rights Reserved.</p>
</div>
</body>
</html>
```